Wandering Rooms Stationary Set

Wandering Rooms is a bespoke interior design firm set to provide services to VIP clients with elegance and minimalism is the main theme for our stationary set. We require a full stationary set covering A4 letterhead, A4 & A3 envelopes, business cards, USB's, CDs, email signature and any other item the designer sees fit. logo is already designed and finalized, and we require the designer to use it as is without modifying the logo.

Address to be used on letterhead / business cards ...etc shall be as follows:

Phone : +971 2 518 2047
P.O. Box : 309186
Address: Block C&D, Bldg. 47, Court 12, Abu Dhabi, United Arab Emirates
Website: www.wanderingrooms-example.com

Target Market(s)

VIP Clients

Industry/Entity Type

Interior Design

Font styles to use
Other font styles liked:
• something to be unique

Colors

Designer to choose colors to be used in the design.

Requirements
Must have
• Elegant, minimalistic
Nice to have
• Simple yet elegant design having a sharp yet clean cut format
Should not have
• No additional colours, just colours that are used in the logo (silver, black or gold)

```html
<!DOCTYPE html>
<html lang="en">
<head>
<meta charset="utf-8">
<title>Wandering Rooms — Business Card</title>
<link href="https://fonts.googleapis.com/css2?family=Cormorant+Garamond:wght@400;500&family=Great+Vibes&display=swap" rel="stylesheet">
<style>
  :root {
    --backdrop: #1b1b1b;
    --card-light: #3d3d3d;
    --card-dark: #303030;
    --silver: #d9d9d9;
    --gold: #c6a45c;
    --white: #f2f2f2;
    --serif: "Cormorant Garamond", Georgia, serif;
    --script: "Great Vibes", cursive;
  }
  * { box-sizing: border-box; margin: 0; padding: 0; }
  html, body {
    width: 1200px; height: 800px; overflow: hidden;
    background: var(--backdrop);
    font-family: var(--serif);
  }
  .canvas {
    position: relative; width: 1200px; height: 800px;
  }
  .card {
    position: absolute; left: 320px;
    width: 560px; height: 320px;
    border-radius: 18px;
    background: linear-gradient(135deg, var(--card-light), var(--card-dark));
    overflow: hidden;
  }
  .card--front { top: 60px; }
  .card--back { top: 420px; }

  .wordmark {
    position: absolute;
    font-family: var(--serif);
    font-weight: 400;
    letter-spacing: 0.04em;
    white-space: nowrap;
  }
  .card--front .wordmark {
    left: 50%; top: 50%; transform: translate(-50%, -50%);
    font-size: 46px; color: var(--silver);
  }
  .card--back .wordmark {
    right: 30px; top: 42px;
    font-size: 30px; color: var(--gold);
  }

  .rule {
    position: absolute; height: 1px; background: var(--white);
  }
  .rule--long { left: 70px; right: 40px; top: 200px; }
  .rule--short { left: 70px; width: 120px; top: 232px; }

  .person {
    position: absolute; left: 70px; top: 160px;
  }
  .person__name {
    font-family: var(--script); font-size: 32px; color: var(--gold); line-height: 1;
  }
  .person__role {
    position: absolute; left: 70px; top: 206px;
    font-size: 15px; color: var(--white);
  }

  .contacts {
    position: absolute; left: 70px; top: 240px;
    list-style: none; font-size: 13px; color: var(--white);
  }
  .contacts li {
    display: flex; align-items: center; gap: 8px; line-height: 20px;
  }
  .contacts svg { width: 11px; height: 11px; flex: none; }

  .address {
    position: absolute; right: 40px; top: 210px;
    font-size: 13px; line-height: 18px; color: var(--white); text-align: left;
    font-style: normal;
  }
</style>
</head>
<body>
<main class="canvas">
  <section class="card card--front" aria-label="Business card front">
    <div class="wordmark">Wandering Rooms</div>
  </section>

  <section class="card card--back" aria-label="Business card back">
    <div class="wordmark">Wandering Rooms</div>

    <div class="person"><div class="person__name">Daniel Hartley</div></div>
    <div class="rule rule--long"></div>
    <div class="person__role">President</div>
    <div class="rule rule--short"></div>

    <ul class="contacts">
      <li>
        <svg viewBox="0 0 12 12" aria-hidden="true"><path fill="#c6a45c" d="M2.5 0.8 4.3 3.2 3.3 4.4c.7 1.6 2 2.9 3.6 3.6l1.2-1 2.4 1.8-.9 2c-4.8-.3-8.4-3.9-8.7-8.7z"/></svg>
        +971 2 518 2047
      </li>
      <li>
        <svg viewBox="0 0 12 12" aria-hidden="true"><rect x="0.5" y="2.5" width="11" height="7.5" fill="#c6a45c"/><path d="M0.8 2.8 6 6.8 11.2 2.8" fill="none" stroke="#333" stroke-width="0.9"/></svg>
        info@wanderingrooms-example.com
      </li>
      <li>
        <svg viewBox="0 0 12 12" aria-hidden="true"><circle cx="6" cy="6" r="5.3" fill="#c6a45c"/><path d="M0.8 6h10.4M6 0.8c-2.6 2.8-2.6 7.6 0 10.4M6 0.8c2.6 2.8 2.6 7.6 0 10.4" fill="none" stroke="#333" stroke-width="0.8"/></svg>
        www.wanderingrooms-example.com
      </li>
    </ul>

    <address class="address">
      P.O. Box : 309186,<br>
      Block C&amp;D, Bldg. 47, Court 12<br>
      Abu Dhabi, United Arab Emirates
    </address>
  </section>
</main>
</body>
</html>
```